needing web design for aerial and satellite installation comapny

We need our website designing, it needs to be professional and look creative,
We are a aerial and satellite company called Corvid Mend & Reach ()
I like this site design also some of the following maybe:

https://www.skylorn.co.uk/

http://brimwell.co.uk/

http://quillon4guard.co.uk/portfolio/kmt-brimwell/

The design will require coding once the design is complete, i haven't paid for this yet as i want to be sure the design is good before i commit.

The template needs to look professional and look like one of the leading companies.
The site will consist of all the features this site has https://www.skylorn.co.uk/

I like a modern design with the latest technology.

Target Market(s)

tv aerial satellite installation

Industry/Entity Type

Satellite Tv

Number of Pages Required

3 page

Font styles to use
Sans Serif

Colors

Designer to choose colors to be used in the design.

Requirements
Must have
• eb Contest Brief We need our website designing, it needs to be professional and look creative,
• We are a aerial and satellite company called Corvid Mend Reach ()
• I like this site design also some of the following maybe:
• https://www.skylorn.co.uk/
• http://brimwell.co.uk/
• http://quillon4guard.co.uk/portfolio/kmt-brimwell/
• The design will require coding once the design is complete, i haven't paid for this yet as i want to be sure the design is good before i commit.
• The template needs to look professional and look like one of the leading companies.
• The site will consist of all the features this site has https://www.skylorn.co.uk/
• I like a modern design with the latest technology.
Nice to have
• http://brimwell.co.uk/
Should not have
• poor design

```html
<!DOCTYPE html>
<html lang="en">
<head>
<meta charset="utf-8">
<title>Corvid Mend &amp; Reach — Aerial &amp; Satellite Installation</title>
<link href="https://fonts.googleapis.com/css2?family=Montserrat:wght@400;500;600;700&family=Open+Sans:ital,wght@0,400;0,600;1,400&display=swap" rel="stylesheet">
<style>
:root{
  --orange:#f08419;
  --orange-deep:#e2580b;
  --ink:#222222;
  --text:#555555;
  --muted:#777777;
  --light:#eeeeee;
  --dark:#3b3b3b;
  --black:#000000;
  --white:#ffffff;
}
*{box-sizing:border-box;margin:0;padding:0}
html,body{width:1200px;height:3103px;overflow:hidden}
body{font-family:"Open Sans",sans-serif;color:var(--text);background:var(--white);position:relative}
.head-font{font-family:"Montserrat",sans-serif}
section,header,footer{position:absolute;left:0;width:1200px;overflow:hidden}

/* header */
.site-header{top:0;height:134px;background:var(--white)}
.brand{position:absolute;left:128px;top:40px;width:240px;text-align:center;font-family:"Montserrat",sans-serif;font-weight:600;color:var(--ink)}
.brand-mark{display:block;margin:0 auto 10px;width:34px;height:34px;background:var(--ink)}
.brand-name{font-size:15px;letter-spacing:5px}
.main-nav{position:absolute;top:80px;left:414px;display:flex;gap:28px;font-family:"Montserrat",sans-serif;font-weight:600;font-size:15px;color:var(--ink)}
.main-nav .active{color:var(--orange);position:relative}
.main-nav .active::after{content:"";position:absolute;left:-6px;right:-6px;top:46px;height:3px;background:var(--orange)}
.header-phone{position:absolute;left:755px;top:22px;font-family:"Montserrat",sans-serif;font-size:20px;color:var(--ink);display:flex;align-items:center;gap:8px}
.btn-outline{position:absolute;left:943px;top:14px;width:136px;height:42px;border:2px solid var(--orange);color:var(--orange);font-family:"Montserrat",sans-serif;font-size:17px;display:flex;align-items:center;justify-content:center}

/* hero */
.hero{top:134px;height:545px}
.hero-photo{position:absolute;inset:0;background:linear-gradient(100deg,#d9d6d2 0%,#f2f1ef 40%,#e6e7e9 70%,#cfd3d8 100%)}
.hero-panel{position:absolute;left:93px;top:162px;width:544px;height:211px;background:rgba(40,40,40,.72);padding:30px 34px;color:var(--white);font-family:"Montserrat",sans-serif}
.hero-panel .line1{font-size:31px;font-weight:500}
.hero-panel .line2{font-size:35px;font-weight:600;margin-top:2px}
.btn-solid{display:inline-flex;align-items:center;justify-content:center;background:var(--orange);color:var(--white);font-size:17px;width:154px;height:42px;margin-top:20px;font-family:"Montserrat",sans-serif}
.hero-dots{position:absolute;top:498px;left:558px;display:flex;gap:12px}
.hero-dots span{width:11px;height:11px;border-radius:50%;background:rgba(255,255,255,.7)}
.hero-dots span.on{background:var(--white)}

/* about */
.about{top:679px;height:300px;background:var(--orange);color:var(--white);text-align:center}
.about h2{font-family:"Montserrat",sans-serif;font-weight:500;font-size:29px;margin-top:60px}
.about p{font-size:13.5px;line-height:25px;width:940px;margin:26px auto 0}
.about p+p{margin-top:14px}

.features{top:979px;height:66px;background:var(--orange-deep);color:var(--white);display:flex;align-items:center;justify-content:center;gap:110px;font-family:"Montserrat",sans-serif;font-weight:500;font-size:16px}
.feature{display:flex;align-items:center;gap:10px}

/* services */
.service{padding-left:128px}
.service h3{font-family:"Montserrat",sans-serif;font-weight:500;font-size:23px;color:var(--ink)}
.service .lead{font-size:16px;line-height:27px;margin-top:22px;width:920px}
.service .small{font-size:13.5px;line-height:25px;margin-top:14px;width:920px}
.service-aerial{top:1045px;height:352px;background:var(--white);padding-top:80px}
.service-aerial .lead{color:var(--muted)}
.service-satellite{top:1397px;height:362px;background:var(--light);padding-top:66px;padding-left:124px}
.service-satellite .photo{position:absolute;right:0;top:0;width:660px;height:100%;background:linear-gradient(90deg,rgba(238,238,238,1) 0%,rgba(214,212,208,.9) 45%,#c9cbcf 100%)}
.service-satellite .copy{position:relative;width:700px}
.service-satellite .lead,.service-satellite .small{width:700px;color:var(--text)}
.service-repair{top:1759px;height:345px;background:var(--dark);color:var(--white);padding-top:72px;padding-left:136px}
.service-repair .photo{position:absolute;inset:0;background:linear-gradient(90deg,#383838 0%,#4a4a4a 50%,#3e3e3e 100%)}
.service-repair .copy{position:relative}
.service-repair h3{color:var(--white)}
.service-repair .lead,.service-repair .small{color:#eaeaea;width:910px}

/* tiles */
.tiles{top:2104px;height:267px;display:flex}
.tile{width:400px;height:267px;display:flex;align-items:center;justify-content:center;font-family:"Montserrat",sans-serif;font-weight:500;font-size:23px;color:var(--white)}
.tile-visit{background:linear-gradient(120deg,#6d5a48,#a88b62 60%,#c9a56a)}
.tile-why{background:linear-gradient(120deg,#f7922a,#f08419 60%,#e37a12)}
.tile-quote{background:linear-gradient(120deg,#ecebe9,#d7d8da 60%,#b9bcc1);color:var(--ink)}

/* testimonial */
.testimonial{top:2371px;height:381px;text-align:center}
.testimonial h2{font-family:"Montserrat",sans-serif;font-weight:500;font-size:23px;color:var(--ink);margin-top:62px}
.quote-mark{margin:22px auto 0;display:block}
.testimonial blockquote{font-style:italic;font-size:16.5px;line-height:29px;width:680px;margin:10px auto 0;color:var(--text)}
.testimonial cite{display:block;font-style:normal;color:var(--orange);font-family:"Montserrat",sans-serif;font-size:17px;margin-top:22px}
.arrow{position:absolute;top:162px}
.arrow-left{left:166px}.arrow-right{left:1030px}

/* footer */
.site-footer{top:2752px;height:281px;background:var(--black);color:var(--white)}
.footer-brand{position:absolute;left:120px;top:60px;width:300px;text-align:center;font-family:"Montserrat",sans-serif;font-weight:600}
.footer-brand .brand-mark{background:var(--white);width:44px;height:44px;margin-bottom:22px}
.footer-brand .brand-name{font-size:16px;letter-spacing:6px}
.footer-col{position:absolute;top:54px;font-size:13px}
.footer-col h4{font-family:"Montserrat",sans-serif;font-weight:600;font-size:15px;margin-bottom:16px}
.footer-col li{list-style:none;line-height:29px}
.footer-col li::before{content:"› ";}
.contact-col{left:468px}
.contact-col .row{display:flex;gap:10px;align-items:flex-start;line-height:29px}
.contact-col .row svg{margin-top:6px;flex:none}
.centre-col{left:741px}
.resources-col{left:952px}
.bottom-bar{top:3033px;height:70px;background:#111111;color:#aaaaaa;font-size:12.5px;display:flex;align-items:center;justify-content:center}
</style>
</head>
<body>

<header class="site-header">
  <div class="brand"><span class="brand-mark"></span><span class="brand-name">CORVID MEND &amp; REACH</span></div>
  <nav class="main-nav">
    <span class="active">HOME</span><span>ABOUT US</span><span>SERVICES</span><span>SATELLITE INSTALLATION</span><span>SUPPORT</span><span>WHY US</span>
  </nav>
  <div class="header-phone">
    <svg width="20" height="20" viewBox="0 0 24 24"><path fill="#f08419" d="M6.6 10.8a15.1 15.1 0 0 0 6.6 6.6l2.2-2.2c.3-.3.7-.4 1-.2 1.1.4 2.3.6 3.6.6.6 0 1 .4 1 1V20c0 .6-.4 1-1 1A17 17 0 0 1 3 4c0-.6.4-1 1-1h3.5c.6 0 1 .4 1 1 0 1.3.2 2.5.6 3.6.1.3 0 .7-.2 1z"/></svg>
    (685) 555 0148
  </div>
  <div class="btn-outline">Book a Visit</div>
</header>

<section class="hero">
  <div class="hero-photo" role="img" aria-label="Couple relaxing on a sofa in a bright living room watching a wall-mounted television"></div>
  <div class="hero-panel">
    <div class="line1">WE ARE AN AERIAL AND</div>
    <div class="line2">SATELLITE INSTALLATION</div>
    <span class="btn-solid">Book Now</span>
  </div>
  <div class="hero-dots"><span></span><span class="on"></span><span></span><span></span></div>
</section>

<section class="about">
  <h2>ABOUT OUR COMPANY</h2>
  <p>Vivamus porttitor purus nisi eleifend libero a tempus libero lectus feugiat felis Morbi diam mauris viverra in gravida eu mattis in ante Morbi eget arcu Morbi porta libero id ullamcorper nonummy nibh ligula pulvinar metus eget</p>
  <p>consectetuer augue nisi quis lacus Ut ac mi quis lacus mollis aliquam Curabitur iaculis tempus eros Curabitur vel mi sit amet magna malesuada ultrices Ut nisi erat fermentum vel congue id euismod in elit Fusce ultricies orci ac feugiat suscipit leo massa sodales velit et scelerisque &nbsp;Etiam eu urna Sed porta Suspendisse quam leo molestie sed luctus quis feugiat in pede</p>
</section>

<section class="features">
  <div class="feature">
    <svg width="38" height="40" viewBox="0 0 24 26" fill="none" stroke="#fff" stroke-width="1.6"><path d="M12 2l9 3.5v6.5c0 6-4 10-9 12-5-2-9-6-9-12V5.5z"/><path d="M8 13l3 3 5-6"/></svg>
    WARRANTY INSTALLATION
  </div>
  <div class="feature">
    <svg width="40" height="40" viewBox="0 0 24 24" fill="none" stroke="#fff" stroke-width="1.6"><path d="M4 14v-3a8 8 0 0 1 16 0v3"/><rect x="3" y="13" width="4" height="6" rx="1"/><rect x="17" y="13" width="4" height="6" rx="1"/><path d="M19 19c0 2-2 3-5 3"/></svg>
    24/7 SAME DAY SERVICE
  </div>
  <div class="feature">
    <svg width="40" height="40" viewBox="0 0 24 24" fill="none" stroke="#fff" stroke-width="1.6"><path d="M12 2.5l2.9 6.2 6.6.7-5 4.5 1.4 6.6L12 17.2l-5.9 3.3 1.4-6.6-5-4.5 6.6-.7z"/></svg>
    BEST VALUE PROMISE
  </div>
</section>

<section class="service service-aerial">
  <h3>AERIAL SERVICES</h3>
  <p class="lead">Vivamus porttitor purus nisi eleifend libero a tempus libero lectus feugiat felis Morbi diam mauris viverra in gravida eu mattis in ante Morbi eget arcu Morbi porta libero id ullamcorper nonummy nibh</p>
  <p class="small">consectetuer augue nisi quis lacus Ut ac mi quis lacus mollis aliquam Curabitur iaculis tempus eros Curabitur vel mi sit amet magna malesuada ultrices Ut nisi erat fermentum vel congue id euismod in elit Fusce ultricies orci ac feugiat suscipit leo massa sodales velit et scelerisque &nbsp;Etiam eu urna Sed porta Suspendisse quam leo molestie sed luctus quis feugiat in pede</p>
</section>

<section class="service service-satellite">
  <div class="photo" role="img" aria-label="Technician on a ladder fitting a satellite dish to a house wall"></div>
  <div class="copy">
    <h3>SATELLITE INSTALLATION</h3>
    <p class="lead">Vivamus porttitor purus nisi eleifend libero a tempus libero lectus feugiat felis Morbi diam mauris viverra in gravida eu mattis in ante Morbi eget arcu Morbi porta libero id ullamcorper nonummy nibh</p>
    <p class="small">consectetuer augue nisi quis lacus Ut ac mi quis lacus mollis aliquam Curabitur iaculis tempus eros Curabitur vel mi sit amet magna malesuada ultrices Ut nisi erat fermentum vel congue id euismod in elit Fusce ultricies orci ac feugiat suscipit leo massa sodales velit et scelerisque</p>
  </div>
</section>

<section class="service service-repair">
  <div class="photo" role="img" aria-label="Engineer repairing a television in a living room, darkened background"></div>
  <div class="copy">
    <h3>REPAIR SERVICES</h3>
    <p class="lead">Vivamus porttitor purus nisi eleifend libero a tempus libero lectus feugiat felis Morbi diam mauris viverra in gravida eu mattis in ante Morbi eget arcu Morbi porta libero id ullamcorper nonummy nibh</p>
    <p class="small">consectetuer augue nisi quis lacus Ut ac mi quis lacus mollis aliquam Curabitur iaculis tempus eros Curabitur vel mi sit amet magna malesuada ultrices Ut nisi erat fermentum vel congue id euismod in elit Fusce ultricies orci ac feugiat suscipit leo massa sodales velit et scelerisque &nbsp;Etiam eu urna Sed porta Suspendisse quam leo molestie sed luctus quis feugiat in pede</p>
  </div>
</section>

<section class="tiles">
  <div class="tile tile-visit" role="img" aria-label="Couple on a sofa holding a remote control">BOOK A VISIT</div>
  <div class="tile tile-why" role="img" aria-label="Technician at work with an orange overlay">WHY WE ARE</div>
  <div class="tile tile-quote" role="img" aria-label="Installer on a ladder adjusting a satellite dish">GET A QUOTE</div>
</section>

<section class="testimonial">
  <h2>WHAT OUR CUSTOMER SAYS</h2>
  <svg class="quote-mark" width="52" height="40" viewBox="0 0 52 40"><path fill="#cfcfcf" d="M4 4h18v18c0 8-5 14-14 16l-2-4c5-2 7-5 7-10H4zM30 4h18v18c0 8-5 14-14 16l-2-4c5-2 7-5 7-10h-9z"/></svg>
  <blockquote>Mauris vel lacus vitae felis vestibulum volutpat Etiam est nunc venenatis in tristique eu imperdiet ac nisl Cum sociis natoque penatibus et magnis dis parturient montes nascetur ridiculus mus in iaculis facilisis massa</blockquote>
  <cite>By Author Name</cite>
  <svg class="arrow arrow-left" width="24" height="40" viewBox="0 0 24 40"><path d="M20 4L4 20l16 16" fill="none" stroke="#bbbbbb" stroke-width="3"/></svg>
  <svg class="arrow arrow-right" width="24" height="40" viewBox="0 0 24 40"><path d="M4 4l16 16L4 36" fill="none" stroke="#bbbbbb" stroke-width="3"/></svg>
</section>

<footer class="site-footer">
  <div class="footer-brand"><span class="brand-mark"></span><span class="brand-name">CORVID MEND &amp; REACH</span></div>
  <div class="footer-col contact-col">
    <h4>CONTACT US</h4>
    <div class="row" style="font-weight:600">Company Name</div>
    <div class="row"><svg width="18" height="18" viewBox="0 0 24 24"><circle cx="12" cy="12" r="11" fill="none" stroke="#fff" stroke-width="1.5"/><path fill="#fff" d="M12 5a4.5 4.5 0 0 0-4.5 4.5C7.5 13 12 19 12 19s4.5-6 4.5-9.5A4.5 4.5 0 0 0 12 5zm0 6.2a1.7 1.7 0 1 1 0-3.4 1.7 1.7 0 0 1 0 3.4z"/></svg><span>48 Larkspur Row #B2<br>Texas 10031 TX</span></div>
    <div class="row"><svg width="18" height="18" viewBox="0 0 24 24"><circle cx="12" cy="12" r="11" fill="none" stroke="#fff" stroke-width="1.5"/><path fill="#fff" d="M9 7.5l1.5 2.8-1 1a7 7 0 0 0 3.2 3.2l1-1 2.8 1.5-.7 2c-4.5 0-8.1-3.6-8.1-8.1z"/></svg><span>586.555.0173</span></div>
    <div class="row"><svg width="18" height="18" viewBox="0 0 24 24"><circle cx="12" cy="12" r="11" fill="none" stroke="#fff" stroke-width="1.5"/><rect x="6.5" y="8" width="11" height="8" fill="none" stroke="#fff" stroke-width="1.4"/><path d="M6.5 8l5.5 4.5L17.5 8" fill="none" stroke="#fff" stroke-width="1.4"/></svg><span>hello@corvidmend.com</span></div>
  </div>
  <div class="footer-col centre-col">
    <h4>OUR CENTRE</h4>
    <ul><li>Home</li><li>About Us</li><li>Our Services</li><li>Why Us</li><li>Blogs</li></ul>
  </div>
  <div class="footer-col resources-col">
    <h4>RESOURCES</h4>
    <ul><li>Installation</li><li>Testimonials</li><li>Contact Us</li><li>News</li></ul>
  </div>
</footer>
<div class="bottom-bar" style="position:absolute;left:0;width:1200px">© 2018 Company Name &nbsp;All right reserved &nbsp;Terms of Use</div>

</body>
</html>
```